Dean Hartwell realestate

We want something complete different to our website now and something that will stand out this is our website http://deanhartwellrealestate.com/

our company website for my boss is www.gordonvale.com

please note this website is being made for dean hartwell not gordon vale

something similar to our company website but has to be in the branding of dean hartwell realestate

```html
<!DOCTYPE html>
<html lang="en">
<head>
<meta charset="utf-8">
<title>Dean Hartwell Property</title>
<link href="https://fonts.googleapis.com/css2?family=Open+Sans:wght@300;400;600;700&display=swap" rel="stylesheet">
<style>
:root{
  --red:#f23a50;
  --dark:#2c2c2c;
  --ink:#1e1e1e;
  --grey:#efefef;
  --field:#e6e6e6;
  --muted:#5a5a5a;
  --white:#ffffff;
}
*{box-sizing:border-box;margin:0;padding:0}
html,body{width:1200px;height:3077px;overflow:hidden}
body{position:relative;background:var(--white);font-family:"Open Sans",sans-serif;color:var(--ink)}
.abs{position:absolute}

/* hero */
.hero-media{left:0;top:111px;width:1200px;height:525px;background:linear-gradient(180deg,#6e8f6a 0%,#4d6a3c 35%,#6f9a3a 62%,#87ae3f 100%)}
.hero-play{left:574px;top:328px;width:52px;height:52px;border-radius:50%;background:rgba(30,30,30,.75);display:flex;align-items:center;justify-content:center}
.hero-edge{left:0;top:530px}

/* header */
.site-header{left:131px;top:8px;width:936px}
.brand{height:78px;background:var(--dark);display:flex;align-items:center;justify-content:center;color:var(--white);font-weight:300;font-size:36px;letter-spacing:.5px}
.main-nav{height:45px;background:var(--red);display:flex;align-items:center;font-size:13px;font-weight:600;color:var(--white);text-transform:uppercase}
.main-nav a{color:inherit;text-decoration:none;height:45px;display:flex;align-items:center;padding:0 24px}
.main-nav a.active{background:#e02c42;padding:0 38px}
.main-nav .call{margin-left:auto;padding-right:38px}

/* sold list */
.section-title{color:var(--red);font-weight:700;font-size:24px;text-transform:uppercase}
.sold-title{left:131px;top:726px}
.listing{left:131px;width:640px;height:199px;background:var(--grey);display:flex}
.listing-photo{width:256px;height:199px}
.listing-body{padding:22px 24px 0 24px}
.listing-body h3{font-size:16px;font-weight:600;text-transform:uppercase;margin-bottom:6px}
.listing-price{color:var(--red);font-size:16px;margin-bottom:9px}
.listing-body p{font-size:10.5px;line-height:17px;color:var(--muted);width:345px}
.features{display:flex;gap:30px;margin-top:16px;font-size:15px;color:#333}
.features span{display:flex;align-items:center;gap:8px}
.btn{background:var(--ink);color:var(--white);font-weight:600;font-size:13px;display:flex;align-items:center;justify-content:center}
.view-all{left:131px;top:1637px;width:97px;height:39px}

/* search */
.search-panel{left:827px;top:714px;width:240px;height:436px;background:var(--red);padding:14px 12px 0}
.search-panel h2{color:var(--white);font-size:22px;font-weight:700;text-transform:uppercase;display:flex;align-items:center;gap:8px;justify-content:center;margin-bottom:14px}
.select{height:38px;background:var(--white);margin-bottom:18px;display:flex;align-items:center;justify-content:space-between;padding:0 14px;font-size:12px;color:#444}
.search-btn{height:38px;font-size:14px;letter-spacing:.5px}
.advanced{display:block;text-align:center;color:var(--white);font-size:12px;text-decoration:underline;margin-top:14px}
.search-edge{left:827px;top:1150px}

/* testimonial */
.quote-band{left:0;top:1756px;width:1200px;height:521px;background:linear-gradient(180deg,#3c3c3c,#2a2a2a 55%,#303030)}
.quote-edge{left:0;top:2150px}
.quote{left:130px;top:1845px;width:940px;text-align:center;color:var(--white)}
.quote h2{color:#f25a6d;font-size:24px;font-weight:700;text-transform:uppercase;margin-bottom:18px}
.quote p{font-size:19px;line-height:36px}
.quote cite{display:block;font-style:normal;font-size:19px;margin-top:18px}
.quote-arrows{display:flex;gap:6px;justify-content:center;margin-top:12px}
.quote-arrows span{width:22px;height:22px;border:1.5px solid var(--white);display:flex;align-items:center;justify-content:center}

/* appraisal */
.appraisal-title{left:131px;top:2364px}
.contact-title{left:888px;top:2364px}
.appraisal-form{left:131px;top:2412px;width:433px}
.field{height:45px;background:var(--field);margin-bottom:11px;display:flex;align-items:center;padding:0 16px;font-size:12px;color:#444}
.submit{width:80px;height:43px;background:var(--red);color:var(--white);font-size:12px;font-weight:700;display:flex;align-items:center;justify-content:center;margin-top:20px}
.contact-card{left:636px;top:2412px;width:431px;height:378px;background:var(--field);padding:8px}
.map{width:415px;height:259px;background:linear-gradient(180deg,#e4e8ec,#d8dde2)}
.contact-lines{font-size:14px;line-height:25px;color:#333;padding:18px 14px 0}

/* footer */
.footer-edge{left:0;top:2880px}
.footer-base{left:0;top:2968px;width:1200px;height:109px;background:var(--dark)}
.social{left:0;top:2928px;width:1200px;display:flex;justify-content:center;gap:14px}
.social span{width:36px;height:36px;border-radius:50%;background:#8a8a8a}
.footer-nav{left:0;top:2993px;width:1200px;text-align:center;font-size:12px;color:var(--white)}
.footer-nav span{margin:0 10px}
.copyright{left:0;top:3022px;width:1200px;text-align:center;font-size:12px;color:#dcdcdc}
</style>
</head>
<body>

<div class="abs hero-media" role="img" aria-label="Video still of the agent standing in a park among carved timber posts"></div>
<div class="abs hero-play"><svg width="20" height="22" viewBox="0 0 20 22"><polygon points="2,1 19,11 2,21" fill="#fff"/></svg></div>
<svg class="abs hero-edge" width="1200" height="106" viewBox="0 0 1200 106">
  <polygon points="0,68 600,20 1200,68 1200,106 0,106" fill="var(--red)"/>
  <polygon points="0,106 600,7 1200,106" fill="var(--white)"/>
</svg>

<header class="abs site-header">
  <div class="brand">Dean Hartwell Property</div>
  <nav class="main-nav">
    <a class="active">Home</a><a>For Sale</a><a>Agents</a><a>Book Appraisal</a><a>Contact</a>
    <a class="call">Call us on : 0400 317 628</a>
  </nav>
</header>

<h2 class="abs section-title sold-title">Latest Properties Sold</h2>

<article class="abs listing" style="top:771px">
  <div class="listing-photo" role="img" aria-label="Single-storey brick home with front garden at dusk" style="background:linear-gradient(180deg,#3d5f9a,#8a5a4a 55%,#6a4a3a)"></div>
  <div class="listing-body">
    <h3>18 Marlow Street Kewdale, 6105</h3>
    <div class="listing-price">From $382,546</div>
    <p>Bright family home close to schools, parks and shops. Recently renovated kitchen, open living and a large rear garden with shaded alfresco area.</p>
    <div class="features"><span><svg width="18" height="12" viewBox="0 0 18 12"><path d="M1 1v10M1 8h16v3M1 6h16M6 3h10v3" stroke="#333" stroke-width="2" fill="none"/></svg>4</span><span><svg width="16" height="12" viewBox="0 0 16 12"><path d="M1 5h14v3a3 3 0 0 1-3 3H4a3 3 0 0 1-3-3zM3 5V1h3" stroke="#333" stroke-width="2" fill="none"/></svg>2</span><span><svg width="18" height="12" viewBox="0 0 18 12"><path d="M2 6l2-5h10l2 5v5H2z" fill="#333"/><circle cx="5" cy="8" r="1.3" fill="#efefef"/><circle cx="13" cy="8" r="1.3" fill="#efefef"/></svg>2</span></div>
  </div>
</article>

<article class="abs listing" style="top:987px">
  <div class="listing-photo" role="img" aria-label="Modern white home with double garage under blue sky" style="background:linear-gradient(180deg,#4a7fc8,#cfd4d8 50%,#9c9a94)"></div>
  <div class="listing-body">
    <h3>27 Ashby Street Lathlain, 6100</h3>
    <div class="listing-price">From $451,215</div>
    <p>Bright family home close to schools, parks and shops. Recently renovated kitchen, open living and a large rear garden with shaded alfresco area.</p>
    <div class="features"><span><svg width="18" height="12" viewBox="0 0 18 12"><path d="M1 1v10M1 8h16v3M1 6h16M6 3h10v3" stroke="#333" stroke-width="2" fill="none"/></svg>4</span><span><svg width="16" height="12" viewBox="0 0 16 12"><path d="M1 5h14v3a3 3 0 0 1-3 3H4a3 3 0 0 1-3-3zM3 5V1h3" stroke="#333" stroke-width="2" fill="none"/></svg>2</span><span><svg width="18" height="12" viewBox="0 0 18 12"><path d="M2 6l2-5h10l2 5v5H2z" fill="#333"/><circle cx="5" cy="8" r="1.3" fill="#efefef"/><circle cx="13" cy="8" r="1.3" fill="#efefef"/></svg>2</span></div>
  </div>
</article>

<article class="abs listing" style="top:1203px">
  <div class="listing-photo" role="img" aria-label="Two-storey red brick townhouse with garage" style="background:linear-gradient(180deg,#3f72c4,#9a5a48 45%,#8a8a86)"></div>
  <div class="listing-body">
    <h3>3/11 Tamsin Road Cloverdale, 6105</h3>
    <div class="listing-price">From $356,952</div>
    <p>Bright family home close to schools, parks and shops. Recently renovated kitchen, open living and a large rear garden with shaded alfresco area.</p>
    <div class="features"><span><svg width="18" height="12" viewBox="0 0 18 12"><path d="M1 1v10M1 8h16v3M1 6h16M6 3h10v3" stroke="#333" stroke-width="2" fill="none"/></svg>4</span><span><svg width="16" height="12" viewBox="0 0 16 12"><path d="M1 5h14v3a3 3 0 0 1-3 3H4a3 3 0 0 1-3-3zM3 5V1h3" stroke="#333" stroke-width="2" fill="none"/></svg>2</span><span><svg width="18" height="12" viewBox="0 0 18 12"><path d="M2 6l2-5h10l2 5v5H2z" fill="#333"/><circle cx="5" cy="8" r="1.3" fill="#efefef"/><circle cx="13" cy="8" r="1.3" fill="#efefef"/></svg>2</span></div>
  </div>
</article>

<article class="abs listing" style="top:1419px">
  <div class="listing-photo" role="img" aria-label="Rendered home with tiled roof and green lawn" style="background:linear-gradient(180deg,#3d78cf,#c9a27a 50%,#6b9a3c)"></div>
  <div class="listing-body">
    <h3>52 Fenwick Street Kewdale, 6105</h3>
    <div class="listing-price">From $481,527</div>
    <p>Bright family home close to schools, parks and shops. Recently renovated kitchen, open living and a large rear garden with shaded alfresco area.</p>
    <div class="features"><span><svg width="18" height="12" viewBox="0 0 18 12"><path d="M1 1v10M1 8h16v3M1 6h16M6 3h10v3" stroke="#333" stroke-width="2" fill="none"/></svg>4</span><span><svg width="16" height="12" viewBox="0 0 16 12"><path d="M1 5h14v3a3 3 0 0 1-3 3H4a3 3 0 0 1-3-3zM3 5V1h3" stroke="#333" stroke-width="2" fill="none"/></svg>2</span><span><svg width="18" height="12" viewBox="0 0 18 12"><path d="M2 6l2-5h10l2 5v5H2z" fill="#333"/><circle cx="5" cy="8" r="1.3" fill="#efefef"/><circle cx="13" cy="8" r="1.3" fill="#efefef"/></svg>2</span></div>
  </div>
</article>

<div class="abs btn view-all">View All</div>

<aside class="abs search-panel">
  <h2><svg width="20" height="20" viewBox="0 0 20 20"><circle cx="8" cy="8" r="6" stroke="#fff" stroke-width="3" fill="none"/><path d="M12.5 12.5L18 18" stroke="#fff" stroke-width="3"/></svg>Search Home</h2>
  <div class="select">Location<svg width="10" height="14" viewBox="0 0 10 14"><path d="M5 13S1 7.5 1 5a4 4 0 0 1 8 0c0 2.5-4 8-4 8z" fill="#222"/><circle cx="5" cy="5" r="1.5" fill="#fff"/></svg></div>
  <div class="select">Home Type<svg width="10" height="6"><polygon points="0,0 10,0 5,6" fill="#222"/></svg></div>
  <div class="select">Price Range<svg width="10" height="6"><polygon points="0,0 10,0 5,6" fill="#222"/></svg></div>
  <div class="select">Sqr.Ft<svg width="10" height="6"><polygon points="0,0 10,0 5,6" fill="#222"/></svg></div>
  <div class="select">Other Features<svg width="10" height="6"><polygon points="0,0 10,0 5,6" fill="#222"/></svg></div>
  <div class="btn search-btn">SEARCH</div>
  <a class="advanced">Advanced Search</a>
</aside>
<svg class="abs search-edge" width="240" height="42" viewBox="0 0 240 42">
  <polygon points="0,0 240,0 240,30 120,4 0,30" fill="var(--red)"/>
  <polygon points="0,30 120,4 240,30 240,40 120,14 0,40" fill="var(--ink)"/>
</svg>

<div class="abs quote-band" role="img" aria-label="Darkened aerial view of a riverside golf course"></div>
<svg class="abs quote-edge" width="1200" height="127" viewBox="0 0 1200 127">
  <polygon points="0,74 600,27 1200,74 1200,127 0,127" fill="var(--red)"/>
  <polygon points="0,127 600,33 1200,127" fill="var(--white)"/>
</svg>
<section class="abs quote">
  <h2>What our clients think</h2>
  <p>“ I found Dean to be different from most agents, in that he listened, and set a marketing program to suit the special features of our property. Eager to do anything to assist with a positive outcome, I'd recommend Dean for properties in the local &nbsp;area. ”</p>
  <cite>- Neil Carver, 6100</cite>
  <div class="quote-arrows">
    <span><svg width="8" height="10"><path d="M6 1L2 5l4 4" stroke="#fff" stroke-width="1.5" fill="none"/></svg></span>
    <span><svg width="8" height="10"><path d="M2 1l4 4-4 4" stroke="#fff" stroke-width="1.5" fill="none"/></svg></span>
  </div>
</section>

<h2 class="abs section-title appraisal-title">Book an Appraisal</h2>
<h2 class="abs section-title contact-title">Contact Info</h2>

<form class="abs appraisal-form">
  <div class="field">Name</div>
  <div class="field">Email</div>
  <div class="field">Phone</div>
  <div class="field">Address</div>
  <div class="field">Preferred Time/Day</div>
  <div class="field">Message</div>
  <div class="submit">SUBMIT</div>
</form>

<div class="abs contact-card">
  <div class="map" role="img" aria-label="Street map showing the office location"></div>
  <div class="contact-lines">
    Suite 12, 8 Larkspur Road, Rivervale, WA 6103 Australia<br>
    Email: dean@gordonvale.com<br>
    Phone: 0400 317 628
  </div>
</div>

<svg class="abs footer-edge" width="1200" height="100" viewBox="0 0 1200 100">
  <polygon points="0,62 600,0 1200,62 1200,100 0,100" fill="var(--red)"/>
  <polygon points="0,88 600,12 1200,88 1200,100 0,100" fill="var(--dark)"/>
</svg>
<div class="abs footer-base"></div>
<div class="abs social"><span></span><span></span><span></span></div>
<nav class="abs footer-nav">Home<span>|</span>For Sale<span>|</span>Agents<span>|</span>Book Appraisal<span>|</span>Contact</nav>
<p class="abs copyright">Copyright © 2018 Dean Hartwell Realestate. &nbsp;All rights reserved.</p>

</body>
</html>
```